Brand Identity Stationary Package

Hello I'm looking for a full branding package for my Property Management Company. I have a logo but looking to have the following
Business Card
Email signature
Facebook cover photo
Letterhead (word.doc)
#10 Envelope
Pocket Folder - link to 9x12 pocket folder design specs https://www.printorbit-example.ca/marketing-materials/presentation-folders
would like everything to match and be brand identifiable. The company looks after residential properties/apartments and some commercial properties. Attached is a zip of the files.
For Business Card
Name: Gareth Lindqvist
Position: Operations Manager
Number: 1 (555) 384-2917
Email: Gareth@harborkey-example.ca
Website: Harborkey-example.ca
Property Management

```html
<!DOCTYPE html>
<html lang="en">
<head>
<meta charset="utf-8">
<title>Harborkey Property Management – Business Card</title>
<link href="https://fonts.googleapis.com/css2?family=Roboto:wght@400;500;700&display=swap" rel="stylesheet">
<style>
  :root {
    --page-bg: #121212;
    --card-top: #2a2b2c;
    --card-bottom: #1b1c1d;
    --brand-green: #7bc043;
    --text-light: #e6e6e6;
    --text-muted: #b9b9b9;
    --divider: #4a4b4c;
  }
  * { margin: 0; padding: 0; box-sizing: border-box; }
  html, body {
    width: 1200px;
    height: 900px;
    overflow: hidden;
    background: var(--page-bg);
    font-family: "Roboto", Arial, sans-serif;
  }
  .canvas {
    width: 1200px;
    height: 900px;
    display: flex;
    align-items: center;
    justify-content: center;
  }
  .business-card {
    position: relative;
    width: 1000px;
    height: 572px;
    background: linear-gradient(160deg, var(--card-top) 0%, var(--card-bottom) 70%);
    border-bottom: 6px solid var(--brand-green);
    display: flex;
    align-items: center;
    box-shadow: 0 20px 50px rgba(0,0,0,0.6);
  }
  .brand-block {
    width: 520px;
    padding-left: 70px;
  }
  .brand-name {
    font-size: 64px;
    font-weight: 700;
    letter-spacing: 4px;
    color: var(--text-light);
    line-height: 1;
  }
  .brand-tagline {
    margin-top: 12px;
    font-size: 18px;
    font-weight: 500;
    letter-spacing: 9px;
    color: var(--text-muted);
    text-transform: uppercase;
  }
  .divider {
    width: 1px;
    height: 320px;
    background: linear-gradient(to bottom, transparent, var(--divider) 20%, var(--divider) 80%, transparent);
  }
  .contact-block {
    padding-left: 50px;
    color: var(--text-light);
  }
  .person-name {
    font-size: 34px;
    font-weight: 700;
    color: var(--brand-green);
    text-transform: uppercase;
    letter-spacing: 1px;
  }
  .person-title {
    font-size: 26px;
    color: var(--text-muted);
    margin-bottom: 18px;
  }
  .address {
    font-size: 25px;
    line-height: 1.3;
    margin-bottom: 10px;
  }
  .contact-line {
    display: flex;
    align-items: center;
    gap: 12px;
    font-size: 25px;
    line-height: 1.45;
  }
  .contact-icon {
    width: 22px;
    height: 22px;
    flex: none;
  }
</style>
</head>
<body>
<main class="canvas">
  <section class="business-card">
    <div class="brand-block">
      <div class="brand-name">HARBORKEY</div>
      <div class="brand-tagline">Property Management</div>
    </div>
    <div class="divider"></div>
    <div class="contact-block">
      <div class="person-name">Gareth Lindqvist</div>
      <div class="person-title">Operations Manager</div>
      <div class="address">48 Cedar Lane Court,<br>Maple Ridge, ON L0X 1A1</div>
      <div class="contact-line">
        <svg class="contact-icon" viewBox="0 0 24 24"><path fill="#7bc043" d="M6.6 10.8a15.1 15.1 0 0 0 6.6 6.6l2.2-2.2c.3-.3.7-.4 1-.2 1.1.4 2.3.6 3.6.6.6 0 1 .4 1 1V20c0 .6-.4 1-1 1A17 17 0 0 1 3 4c0-.6.4-1 1-1h3.5c.6 0 1 .4 1 1 0 1.3.2 2.5.6 3.6.1.3 0 .7-.2 1z"/></svg>
        <span>1 (555) 384-2917</span>
      </div>
      <div class="contact-line">
        <svg class="contact-icon" viewBox="0 0 24 24"><rect x="2" y="5" width="20" height="14" rx="1" fill="#7bc043"/><path d="M2.5 5.5 12 13l9.5-7.5" fill="none" stroke="#1e1f20" stroke-width="1.6"/></svg>
        <span>Gareth@harborkey-example.ca</span>
      </div>
      <div class="contact-line">
        <svg class="contact-icon" viewBox="0 0 24 24"><g fill="none" stroke="#7bc043" stroke-width="1.8"><circle cx="12" cy="12" r="9.5"/><ellipse cx="12" cy="12" rx="4" ry="9.5"/><path d="M2.5 12h19M4 7h16M4 17h16"/></g></svg>
        <span>www.harborkey-example.ca</span>
      </div>
    </div>
  </section>
</main>
</body>
</html>
```